Lotus Ridge Website

We need a website that has clean, asian looking images that relax and motivate people to come into our integrated medical center. My current website is www.needlecalmharbor.com and I would like the design for Lotus Ridge Wellness Partners to be similar but more inviting with video content and a product purchase store as well. A moving banner would be nice too. When people are looking for ways of losing weight or getting out of pain we want them to make the connection that we have the solution. This website needs to provide sufficient information so that patients are well informed and choose us as their health provider before they ever walk through our doors. We offer comprehensive natural medicine that is based on the principles that the body can heal itself when given the right conditions. Our services include medical weight loss and hormone balancing, acupuncture and chinese herbal medicine, physical medicine, trigger point injections, allergy testing and joint rehabilitation. The Medical Doctor and Licensed Acupuncturist work as a team to provide optimal care that is catered to each individual who comes through our doors.
Updates

Target Market(s)

40 to 50 year olds who want to lose weight or have pain issues.

Industry/Entity Type

Medical

Requirements
Must have
• Use photos from our website www.needlecalmharbor.com or similar content. Video content. Moving banner with relaxing images.
Nice to have
• Happy, healthy looking people. Medical Doctors working as a team. Friendly staff in a cutting edge facility.
Should not have
• Papyrus font, or big bold words.

```html
<!DOCTYPE html>
<html lang="en">
<head>
<meta charset="utf-8">
<title>Lotus Ridge Website</title>
<link rel="stylesheet" href="https://fonts.googleapis.com/css2?family=Questrial&family=Source+Sans+3:ital,wght@0,400;0,600;1,400&display=swap">
<style>
:root{
  --olive:#a9af2c;
  --olive-light:#b8bd3c;
  --olive-dark:#959b1c;
  --heading:#7e9a2b;
  --lead:#86a534;
  --text:#555;
  --accent:#e0561c;
  --link-blue:#3a7fb0;
  --rule:#cfcfcf;
  --page:#f1f1f1;
  --white:#fff;
}
*{margin:0;padding:0;box-sizing:border-box}
html,body{width:931px;height:1200px;overflow:hidden;background:var(--page)}
body{font-family:"Source Sans 3",Arial,sans-serif;color:var(--text)}
.canvas{position:relative;width:931px;height:1200px;overflow:hidden;
  background:linear-gradient(#f3f3f3 0,#e6e6e6 10px,var(--white) 10px,var(--white) 125px,#fff 125px,#f0f0f0 300px,#e9e9e9 490px,#f4f4f4 700px)}
.abs{position:absolute}
.head-font{font-family:"Questrial","Century Gothic",sans-serif}

/* header */
.brand{left:20px;top:28px;width:173px;height:88px;background:var(--white);display:flex;align-items:center;gap:10px;padding-left:36px}
.brand-mark{width:14px;height:14px;background:var(--olive-dark)}
.brand-name{font-family:"Questrial",sans-serif;font-size:20px;color:#5d6320}
.top-links{right:63px;top:16px;font-size:11px;color:var(--link-blue);letter-spacing:.2px}
.top-links span{color:#999;margin:0 4px}
.touch{right:117px;top:87px;font-size:12px;color:var(--link-blue);font-family:"Questrial",sans-serif}
.social{top:80px;width:21px;height:21px;border-radius:3px}
.social.one{left:825px;background:#4aa8e0}
.social.two{left:851px;background:#4264a8}

/* nav */
.nav{left:0;top:125px;width:931px;height:47px;background:linear-gradient(var(--olive-light),var(--olive-dark))}
.nav-item{top:0;height:47px;line-height:45px;color:var(--white);font-family:"Questrial",sans-serif;font-size:14px}
.nav-sep{top:4px;height:40px;border-left:1px dotted rgba(255,255,255,.7)}

/* hero */
.hero{left:38px;top:172px;width:860px;height:320px;border:1px solid #ccc;
  background:linear-gradient(100deg,#d8dcdc 0%,#f2f2f0 30%,#e6e8e6 55%,#c9cdcc 100%)}
.dropdown{left:310px;top:172px;width:179px;height:165px;background:var(--olive);padding:7px 20px 0 12px}
.dropdown li{list-style:none;color:var(--white);font-size:12.5px;height:20.7px;line-height:19px;border-bottom:1px solid rgba(255,255,255,.55);padding-left:15px;position:relative}
.dropdown li:last-child{border-bottom:0}
.dropdown li::before{content:"";position:absolute;left:1px;top:7px;border-left:4px solid #fff;border-top:3px solid transparent;border-bottom:3px solid transparent}

/* main panel */
.panel{left:40px;top:493px;width:857px;height:625px;background:var(--white)}
.welcome{left:60px;top:516px;font-size:21px;color:var(--heading)}
.intro{left:60px;top:550px;width:555px;font-size:10px;line-height:16.2px}
.intro p{margin-bottom:7px}
.intro .lead{color:var(--lead)}
.sec-title{font-size:18px;color:var(--heading);padding-bottom:4px;border-bottom:1px solid var(--rule)}
.videos-title{left:62px;top:757px;width:213px}
.blog-title{left:343px;top:757px;width:215px}
.video{left:61px;top:795px;width:233px;height:154px;background:linear-gradient(#3a5a2c,#6f8d4f 60%,#2e3a27)}
.video-bar{left:64px;top:921px;width:222px;height:24px;background:rgba(0,0,0,.7);border-radius:2px}
.video-track{left:113px;top:931px;width:130px;height:4px;background:#5e9a2e}
.play{left:78px;top:927px}
.about-video{left:64px;top:958px;font-size:12.5px;color:#444}
.about-text{left:64px;top:978px;width:215px;font-size:10px;line-height:16px}
.blog-list{left:345px;top:795px;width:240px;font-size:10px;line-height:16px}
.blog-item{margin-bottom:11px}
.blog-item u{color:#666}
.more{display:block;color:var(--accent);font-style:italic;margin-top:1px}

/* sidebar */
.shop-bar{left:645px;top:510px;width:253px;height:33px;background:linear-gradient(90deg,var(--olive),var(--olive-dark));color:var(--white);font-family:"Questrial",sans-serif;font-size:18px;line-height:33px;padding-left:16px}
.product{width:107px;height:92px;border:1px solid #ccc;padding:3px;background:var(--white)}
.product div{width:100%;height:100%}
.btn{border:1px solid #c9c9c9;border-radius:4px;color:var(--link-blue);font-size:10px;letter-spacing:.2px;text-align:center;background:linear-gradient(#fff,#f1f1f1)}
.stories{left:653px;top:819px;font-size:19px;color:var(--heading)}
.quote{font-size:10px;line-height:16px;color:#555;font-style:italic;width:222px}
.qmark{color:var(--accent);font-size:24px;font-style:italic;font-family:Georgia,serif;line-height:1}

/* footer */
.footer{left:0;top:1118px;width:931px;height:82px;background:var(--olive)}
.foot-nav{left:57px;top:1131px;font-size:12px;color:var(--white);word-spacing:0}
.foot-nav span{margin-right:19px}
.copyright{left:58px;top:1161px;font-size:10px;color:#eef0c8}
</style>
</head>
<body>
<div class="canvas">

  <header>
    <div class="abs brand"><span class="brand-mark"></span><span class="brand-name">Lotus Ridge</span></div>
    <div class="abs top-links">REGISTER<span>|</span>SIGN UP<span>|</span>VIDEOS</div>
    <div class="abs touch">GET IN TOUCH WITH</div>
    <span class="abs social one" role="img" aria-label="Social profile link"></span>
    <span class="abs social two" role="img" aria-label="Social profile link"></span>
  </header>

  <nav class="abs nav">
    <span class="abs nav-item" style="left:68px">Main</span>
    <span class="abs nav-sep" style="left:113px"></span>
    <span class="abs nav-item" style="left:128px">Seitai Shinpo</span>
    <span class="abs nav-sep" style="left:223px"></span>
    <span class="abs nav-item" style="left:238px">About Us</span>
    <span class="abs nav-sep" style="left:309px"></span>
    <span class="abs nav-item" style="left:324px">Services</span>
    <span class="abs nav-sep" style="left:389px"></span>
    <span class="abs nav-item" style="left:404px">Biography</span>
    <span class="abs nav-sep" style="left:480px"></span>
    <span class="abs nav-item" style="left:499px">Acupuncture</span>
    <span class="abs nav-sep" style="left:596px"></span>
    <span class="abs nav-item" style="left:612px">Nutrition</span>
    <span class="abs nav-sep" style="left:683px"></span>
    <span class="abs nav-item" style="left:695px">My Jorney</span>
    <span class="abs nav-sep" style="left:773px"></span>
    <span class="abs nav-item" style="left:789px">Contact Us</span>
  </nav>

  <div class="abs hero" role="img" aria-label="Banner photo of a woman exercising on a rowing machine in a bright gym"></div>
  <ul class="abs dropdown">
    <li>Medical weight loss</li>
    <li>Hormone balancing</li>
    <li>Acupuncture</li>
    <li>Chinese herbal medicine</li>
    <li>Physical medicine</li>
    <li>Trigger point injections</li>
    <li>Allergy testing</li>
  </ul>

  <main>
    <div class="abs panel"></div>

    <h1 class="abs welcome head-font" style="font-weight:400">Welcome to Our Website Mainpage</h1>
    <div class="abs intro">
      <p class="lead">Brightwave Studio is a web service company, offering a wide range of services which range from designing and development, that is covering almost all the fields in the best possible way. To be the best we know what and how to present beautifully the working of the client's need and their advantages be highlighted. We act in accordance with the Industry certified processes to deliver the best to our clients all over the world. Over years we have built a strong reputation in providing website design and web development services.</p>
      <p>Thus, Wanna get ahead in the competition with other websites…. Brightwave Studio provide you with an attractive and most convincing website to enhance your marketing goals.</p>
      <p>The only way to success is through the right path and that's what we provide you. None of the other companies has the result we do. So stick to the best that's how you will be the best don't opt for the second best. Our expertise does not limit itself</p>
    </div>

    <h2 class="abs sec-title videos-title head-font" style="font-weight:400">Check Out Our Videos</h2>
    <div class="abs video" role="img" aria-label="Video still of a nurse giving a short introduction outdoors"></div>
    <div class="abs video-bar"></div>
    <svg class="abs play" width="12" height="12" viewBox="0 0 12 12"><path d="M2 1 L11 6 L2 11 Z" fill="#fff"/></svg>
    <div class="abs video-track"></div>
    <h3 class="abs about-video" style="font-weight:400">About Video</h3>
    <p class="abs about-text">Brightwave Studio is a professional website design company dedicated to provide excellent services. We at Brightwave Studio think graphic design as a combination and collaboration of ideas and technology.</p>

    <h2 class="abs sec-title blog-title head-font" style="font-weight:400">Recent Blog &amp; Articles</h2>
    <div class="abs blog-list">
      <div class="blog-item"><u>The only way to success is through </u>the right path and that's what we provide you. None of the other companies has the result<span class="more">read more here</span></div>
      <div class="blog-item"><u>The only way to success is through </u>the right path and that's what we provide you. None of the other companies has the result<span class="more">read more here</span></div>
      <div class="blog-item"><u>The only way to success is through </u>the right path and that's what we provide you.<span class="more">read more here</span></div>
      <div class="blog-item" style="margin-top:16px"><u>The only way to success is through </u>the right path and that's what we provide you.<span class="more">read more here</span></div>
    </div>

    <aside>
      <h2 class="abs shop-bar" style="font-weight:400">Online Products Buy</h2>
      <div class="abs product" style="left:655px;top:553px"><div role="img" aria-label="Product photo of a supplement bottle" style="background:linear-gradient(#1f4c9a,#f0c21a)"></div></div>
      <div class="abs product" style="left:772px;top:553px"><div role="img" aria-label="Product photo of two supplement jars" style="background:linear-gradient(90deg,#e8ecef,#b9c8d8,#f2d24a)"></div></div>
      <div class="abs product" style="left:655px;top:654px"><div role="img" aria-label="Product photo of a green label capsule bottle" style="background:linear-gradient(#e9ebe4,#4f9a3a 70%,#eef0ea)"></div></div>
      <div class="abs product" style="left:772px;top:654px"><div role="img" aria-label="Product photo of a white capsule bottle" style="background:linear-gradient(#f1f1f1,#dfe3ea 60%,#d43a3a)"></div></div>
      <div class="abs btn" style="left:655px;top:765px;width:127px;height:23px;line-height:21px">VIEW MORE PRODUCTS</div>

      <h2 class="abs stories head-font" style="font-weight:400">Success Stories</h2>
      <span class="abs qmark" style="left:643px;top:851px">“</span>
      <p class="abs quote" style="left:660px;top:857px">Brightwave Studio is a professional website design company dedicated to provide excellent services. We at Brightwave Studio think graphic design as a combination and collaboration of ideas and technology.</p>
      <div class="abs btn" style="left:660px;top:948px;width:100px;height:23px;line-height:21px">READ MORE HERE</div>
      <span class="abs qmark" style="left:641px;top:991px">“</span>
      <p class="abs quote" style="left:658px;top:997px">Brightwave Studio is a professional website design company dedicated to provide excellent services. We at Brightwave Studio think graphic design</p>
      <div class="abs btn" style="left:657px;top:1071px;width:100px;height:23px;line-height:21px">READ MORE HERE</div>
    </aside>
  </main>

  <footer class="abs footer"></footer>
  <div class="abs foot-nav"><span>Main</span><span>Seitai Shinpo</span><span>About Us</span><span>Services</span><span>Biography</span><span>Acupuncture</span><span>Nutrition</span><span>My Jorney</span><span>Contact Us</span></div>
  <div class="abs copyright">Copyright © 2012 Company Name &nbsp;|&nbsp; All right reserved</div>

</div>
</body>
</html>
```